Dynamic Business Card for Sports Supplements Company

Hi! I'm looking for an awesome business card to match my existing sports supplement company. I have uploaded my current company logo and screenshot of the front page of my website.

I would like to have something dynamic and interesting and utilize the colors in the website - the reds and purples

The business card should be double sided and focus on a unique eye-catching design on the back and include all the relevant company info.

Most importantly, it should say somewhere: "Sign up on our website for a coupon code."

Target Market(s)

Mostly for women gym goers but it shouldn't be too feminine. It should be in keeping with the website design. It should flow and clearly be connected to it

Industry/Entity Type

Business

Contact Information for Business Card

Lorraine K. Vestal
CEO
LVestal@Quorvanexco.com
www.quorvanexco.com
555.417.3820
P.O. Box 47315
Alderbrook, Westmere 00000

Sign up on our website for a coupon code

Font styles to use
Serif
Sans Serif
Other font styles liked:
• Novecento font family and "Quorvanex" is in AR Destine font

Requirements
Must have
• One side should be a bold Quorvanex logo design. Even just the symbol itself may be o.k. (see attached file)

```html
<!DOCTYPE html>
<html lang="en">
<head>
<meta charset="utf-8">
<title>Quorvanex Business Card</title>
<link href="https://fonts.googleapis.com/css2?family=Lato:wght@400;700;900&display=swap" rel="stylesheet">
<style>
  :root {
    --ink: #161616;
    --paper: #f1f1f1;
    --red: #d4202a;
    --stage: #3a3a3a;
    --muted: #d8d8d8;
  }
  * { box-sizing: border-box; margin: 0; padding: 0; }
  html, body { width: 1200px; height: 834px; overflow: hidden; }
  body {
    background: var(--stage);
    font-family: "Lato", sans-serif;
    display: flex;
    align-items: center;
    justify-content: center;
    gap: 40px;
  }
  .card {
    position: relative;
    width: 540px;
    height: 309px;
    overflow: hidden;
    box-shadow: 0 10px 30px rgba(0,0,0,.45);
  }
  .wordmark {
    position: absolute;
    left: 0; right: 0;
    display: flex;
    align-items: center;
    justify-content: center;
    gap: 12px;
    font-weight: 900;
    font-size: 34px;
    letter-spacing: 1px;
    text-transform: uppercase;
  }
  .wordmark .mark-square {
    width: 26px; height: 26px;
    background: var(--red);
  }

  /* Front side */
  .card-front { background: var(--ink); }
  .card-front .wordmark { top: 92px; color: var(--paper); }
  .card-front .coupon-band {
    position: absolute;
    left: 0; right: 0;
    top: 196px;
    height: 60px;
    background: var(--paper);
    display: flex;
    align-items: flex-start;
    justify-content: center;
    padding-top: 6px;
  }
  .coupon-band p {
    color: var(--red);
    font-size: 14px;
  }

  /* Back side */
  .card-back { background: var(--paper); }
  .card-back .wordmark { top: 78px; color: var(--ink); }
  .card-back .info-band {
    position: absolute;
    left: 0; right: 0;
    top: 152px;
    height: 118px;
    background: var(--ink);
    color: var(--muted);
  }
  .person {
    position: absolute;
    left: 40px;
    bottom: 22px;
  }
  .person .name { font-size: 13px; font-weight: 700; color: var(--paper); }
  .person .role { font-size: 13px; color: var(--red); }
  .contact {
    position: absolute;
    left: 270px;
    top: 14px;
    font-size: 12.5px;
    line-height: 17px;
    list-style: none;
    white-space: nowrap;
  }
  .contact li { display: flex; align-items: center; gap: 8px; }
  .contact svg { width: 12px; height: 12px; flex: none; }
</style>
</head>
<body>

  <section class="card card-front" aria-label="Card front">
    <div class="wordmark"><span class="mark-square"></span>Quorvanex</div>
    <div class="coupon-band">
      <p>Sign up on our website for a coupon code</p>
    </div>
  </section>

  <section class="card card-back" aria-label="Card back">
    <div class="wordmark"><span class="mark-square"></span>Quorvanex</div>
    <div class="info-band">
      <div class="person">
        <p class="name">Lorraine K. Vestal</p>
        <p class="role">CEO</p>
      </div>
      <ul class="contact">
        <li>P.O. Box 47315</li>
        <li>Alderbrook, Westmere 00000</li>
        <li>
          <svg viewBox="0 0 12 12" aria-hidden="true"><path d="M2.5 1 L4.5 1 L5.3 3.5 L4 4.4 Q5 6.8 7.6 8 L8.5 6.7 L11 7.5 L11 9.5 Q10.5 11 9 11 Q1 10 1 2.5 Q1 1 2.5 1Z" fill="var(--red)"/></svg>
          555.417.3820
        </li>
        <li>
          <svg viewBox="0 0 12 12" aria-hidden="true"><rect x="1" y="2.5" width="10" height="7" fill="none" stroke="var(--red)" stroke-width="1.2"/><path d="M1 2.5 L6 6.5 L11 2.5" fill="none" stroke="var(--red)" stroke-width="1.2"/></svg>
          LVestal@Quorvanexco.com
        </li>
        <li>
          <svg viewBox="0 0 12 12" aria-hidden="true"><circle cx="6" cy="6" r="5" fill="none" stroke="var(--red)" stroke-width="1.2"/><ellipse cx="6" cy="6" rx="2.2" ry="5" fill="none" stroke="var(--red)" stroke-width="1"/><path d="M1 6 H11" stroke="var(--red)" stroke-width="1"/></svg>
          www.quorvanexco.com
        </li>
      </ul>
    </div>
  </section>

</body>
</html>
```